Falkrin homes and renovations business card design.

Would like some new card designs utilizing my new logo that look professional. I am open to different colors on the logo or utilize the same ones we have. I like the original concept but would like to see some fresh ideas and build on what we have already done.

Target Market(s)

Custom home building industry, Real estate sales, Renovation projects.

Industry/Entity Type

Home Builder

Contact Information for Business Card

Falkrin Homes and Renovations
2871 96th Avenue
Larrow, Westvale
T2R3W8
Home : 403- 718-4063 Cell: 403- 294-5170

My info is : Dax Falkrin, President and CEO
email: falkrinhomes@maildrop-example.net
Website: falkrinhomes-example.com
websit

Requirements
Must have
• Must Use my new logo design. I am open to different colors on the logo or utilize the same ones in the existing design. I can upload the original logo design if needed.

```html
<!DOCTYPE html>
<html lang="en">
<head>
<meta charset="utf-8">
<title>Falkrin Homes and Renovations – Business Card</title>
<link rel="stylesheet" href="https://fonts.googleapis.com/css2?family=Montserrat:wght@400;500;700&display=swap">
<style>
  :root {
    --stage: #2b2b2b;
    --card-black: #060606;
    --card-white: #ffffff;
    --gold: #b8873a;
    --yellow: #f6b921;
    --grey: #8f8f8f;
    --text-light: #ffffff;
  }
  * { box-sizing: border-box; margin: 0; padding: 0; }
  html, body {
    width: 1200px; height: 864px; overflow: hidden;
    background: var(--stage);
    font-family: "Montserrat", Arial, sans-serif;
  }
  .stage { position: relative; width: 1200px; height: 864px; }
  .card {
    position: absolute; top: 277px;
    width: 540px; height: 309px;
    border-radius: 16px; overflow: hidden;
    box-shadow: 0 12px 30px rgba(0,0,0,.45);
  }
  .card--front { left: 40px; background: var(--card-black); }
  .card--back { left: 620px; background: var(--card-white); }

  .brand { position: absolute; display: flex; align-items: center; gap: 10px; }
  .brand__mark { width: 14px; height: 14px; background: var(--gold); flex: none; }
  .brand__name {
    color: var(--gold); font-weight: 700; text-transform: uppercase;
    line-height: 1.15; letter-spacing: .04em;
  }
  .card--front .brand { left: 50%; top: 108px; transform: translateX(-50%); }
  .card--front .brand__name { font-size: 26px; }
  .card--front .brand__name span { display: block; font-size: 13px; letter-spacing: .12em; }
  .front__url {
    position: absolute; left: 0; right: 0; top: 218px;
    text-align: center; color: var(--text-light); font-size: 13px; letter-spacing: .03em;
  }

  .back__bands { position: absolute; inset: 0; }
  .card--back .brand { right: 28px; top: 30px; }
  .card--back .brand__name { font-size: 22px; text-align: right; }
  .card--back .brand__name span { display: block; font-size: 11px; letter-spacing: .1em; }

  .person { position: absolute; left: 28px; top: 168px; }
  .person__name { color: var(--yellow); font-weight: 700; font-size: 20px; }
  .person__title { color: var(--text-light); font-size: 13px; margin-top: 2px; }
  .contacts { list-style: none; margin-top: 12px; }
  .contacts li {
    display: flex; align-items: center; gap: 8px;
    color: var(--text-light); font-size: 13px; line-height: 19px;
  }
  .contacts svg { width: 13px; height: 13px; flex: none; fill: var(--yellow); }
  .address {
    position: absolute; right: 28px; top: 172px;
    text-align: right; color: var(--text-light); font-size: 13px; line-height: 19px;
    font-style: normal;
  }
</style>
</head>
<body>
<main class="stage">

  <section class="card card--front" aria-label="Card front">
    <div class="brand">
      <div class="brand__mark"></div>
      <div class="brand__name">Falkrin<span>Homes and Renovations</span></div>
    </div>
    <p class="front__url">www.falkrinhomes-example.com</p>
  </section>

  <section class="card card--back" aria-label="Card back">
    <svg class="back__bands" viewBox="0 0 540 309" preserveAspectRatio="none" aria-hidden="true">
      <path d="M0,58 C110,130 330,140 540,88 L540,96 C330,150 110,142 0,78 Z" fill="var(--yellow)"/>
      <path d="M0,62 C110,138 330,148 540,104 L540,309 L0,309 Z" fill="var(--gold)"/>
      <path d="M0,60 C110,134 330,144 540,96 L540,102 C330,146 110,138 0,64 Z" fill="var(--card-white)"/>
    </svg>

    <div class="brand">
      <div class="brand__mark"></div>
      <div class="brand__name">Falkrin<span>Homes and Renovations</span></div>
    </div>

    <div class="person">
      <p class="person__name">Dax Falkrin</p>
      <p class="person__title">President and CEO</p>
      <ul class="contacts">
        <li>
          <svg viewBox="0 0 24 24"><path d="M6.6 10.8a15.1 15.1 0 0 0 6.6 6.6l2.2-2.2a1 1 0 0 1 1-.25 11.4 11.4 0 0 0 3.6.57 1 1 0 0 1 1 1V20a1 1 0 0 1-1 1A17 17 0 0 1 3 4a1 1 0 0 1 1-1h3.5a1 1 0 0 1 1 1c0 1.25.2 2.450.57 3.57a1 1 0 0 1-.25 1z"/></svg>
          403- 718-4063
        </li>
        <li>
          <svg viewBox="0 0 24 24"><path d="M7 1h10a2 2 0 0 1 2 2v18a2 2 0 0 1-2 2H7a2 2 0 0 1-2-2V3a2 2 0 0 1 2-2zm0 3v14h10V4zm5 15.5a1.2 1.2 0 1 0 0 2.4 1.2 1.2 0 0 0 0-2.4z"/></svg>
          403- 294-5170
        </li>
        <li>
          <svg viewBox="0 0 24 24"><path d="M2 5h20v14H2zm2 2v.5l8 5 8-5V7zm0 2.9V17h16V9.9l-8 5z"/></svg>
          falkrinhomes@maildrop-example.net
        </li>
        <li>
          <svg viewBox="0 0 24 24"><path d="M12 2a10 10 0 1 0 0 20 10 10 0 0 0 0-20zm6.9 6h-2.9a15 15 0 0 0-1.4-3.6A8 8 0 0 1 18.9 8zM12 4a13 13 0 0 1 1.9 4h-3.8A13 13 0 0 1 12 4zM4.3 14a8 8 0 0 1 0-4h3.4a16 16 0 0 0 0 4zm.8 2h2.9a15 15 0 0 0 1.4 3.6A8 8 0 0 1 5.1 16zM8 8H5.1a8 8 0 0 1 4.3-3.6A15 15 0 0 0 8 8zm4 12a13 13 0 0 1-1.9-4h3.8A13 13 0 0 1 12 20zm2.3-6H9.7a14 14 0 0 1 0-4h4.6a14 14 0 0 1 0 4zm.3 5.6A15 15 0 0 0 16 16h2.9a8 8 0 0 1-4.3 3.6zM16.3 14a16 16 0 0 0 0-4h3.4a8 8 0 0 1 0 4z"/></svg>
          falkrinhomes-example.com
        </li>
      </ul>
    </div>

    <address class="address">
      2871 96th Avenue<br>
      Larrow, Westvale, T2R3W8
    </address>
  </section>

</main>
</body>
</html>
```